New Design for Willow Glow & Laser

The name of our company is Willow Glow & Laser, and this is our current website: www.WillowGlowLaser.example. We are looking for a fresh design mock-up of our website.
What is important to us?
> We want to maintain the same navigation.
> We want to use the same content (e.g., text, pictures, etc.)
> We want to maintain the color scheme.
> The website aims to get visitors to BOOK ONLINE or BUY ONLINE.
Essential instructions for designers:
> Please visit our current website and our social media accounts to get a better idea of our brand design.
> We want a mockup design for our home page, service page, pricing page, before & after page, shop deals page, careers page, contact pages, and blog pages.
> Color codes: #faa641, #222222, #fffffe, #ea8103
Target Market(s)
women 25 - 45
Number of Pages Required
5+ page

```html
<!DOCTYPE html>
<html lang="en">
<head>
<meta charset="utf-8">
<title>Willow Glow &amp; Laser — Home</title>
<link rel="stylesheet" href="https://fonts.googleapis.com/css2?family=Baloo+2:wght@600;700;800&family=Arimo:ital,wght@0,400;0,700;1,400&display=swap">
<style>
:root{
  --orange:#faa641;
  --orange-deep:#ea8103;
  --dark:#222222;
  --white:#fffffe;
  --grey:#cfcfcf;
  --text:#2b2b2b;
}
*{box-sizing:border-box;margin:0;padding:0}
html,body{width:1200px;height:3361px;overflow:hidden}
body{position:relative;background:var(--white);font-family:"Arimo",Arial,sans-serif;color:var(--text)}
.abs{position:absolute}
.heading{font-family:"Baloo 2",sans-serif;font-weight:700}
.btn{position:absolute;display:flex;align-items:center;justify-content:center;border-radius:20px;font-size:15px;font-family:"Arimo",Arial,sans-serif}
.btn-orange{background:var(--orange);color:var(--dark);box-shadow:0 3px 6px rgba(234,129,3,.35)}
.btn-ghost{border:2px solid var(--orange);color:var(--white)}
.btn-dark{background:var(--dark);color:var(--orange)}

/* photo areas: soft gradients in each photo's main tones */
.photo{overflow:hidden}
.hero-photo{left:0;top:0;width:1200px;height:640px;
  background:
    radial-gradient(ellipse 420px 300px at 760px 300px,rgba(236,214,200,.95),rgba(236,214,200,0) 70%),
    radial-gradient(ellipse 360px 220px at 900px 160px,rgba(250,250,248,.9),rgba(250,250,248,0) 70%),
    radial-gradient(ellipse 300px 180px at 520px 430px,rgba(40,40,42,.85),rgba(40,40,42,0) 70%),
    radial-gradient(ellipse 260px 200px at 1120px 90px,rgba(205,205,205,.9),rgba(205,205,205,0) 70%),
    linear-gradient(110deg,#4c4847 0%,#6f6a67 30%,#b9b1ab 55%,#d8d0ca 75%,#c3bdb9 100%)}
.hero-shade{left:0;top:0;width:1200px;height:640px;background:linear-gradient(90deg,rgba(20,20,20,.55) 0%,rgba(20,20,20,.25) 40%,rgba(0,0,0,0) 62%)}
.nav{left:111px;top:23px;width:978px;height:84px;background:var(--white);border-radius:42px;border-bottom:4px solid var(--orange);box-shadow:0 4px 10px rgba(0,0,0,.12)}
.brand{position:absolute;display:flex;align-items:center;gap:10px;font-family:"Baloo 2",sans-serif;font-weight:800;letter-spacing:1px}
.brand-dot{width:26px;height:26px;border-radius:50%;background:var(--orange)}
.nav-links{position:absolute;left:416px;top:30px;display:flex;gap:19px;font-size:15px;color:var(--dark)}
.hero-title{left:111px;top:234px;font-size:38px;line-height:50px;color:var(--white)}
.hero-title span{color:var(--orange)}
.hero-sub{left:111px;top:298px;width:360px;font-size:16px;line-height:25px;color:var(--white)}
.round-icon{position:absolute;width:62px;height:62px;border-radius:50%;background:var(--white);border:5px solid #f6d3a6;display:flex;align-items:center;justify-content:center}

/* sections */
.section-title{width:1200px;left:0;text-align:center;font-size:35px;color:var(--orange)}
.card-img{width:229px;height:225px}
.card-title{width:229px;text-align:center;font-weight:700;font-size:22px;color:var(--dark)}
.card-line{width:70px;height:2px;background:var(--orange)}

.about-band{left:0;top:1211px;width:1200px;height:527px;background:linear-gradient(135deg,#fbb055 0%,#faa641 60%,#f7a03a 100%)}
.about-title{left:638px;top:1288px;font-size:35px;color:var(--white)}
.about-text{left:638px;top:1345px;width:451px;font-size:15px;line-height:25px;color:var(--dark);text-align:justify}
.about-text p+p{margin-top:10px}

.quote-badge{position:absolute;width:100px;height:100px;border-radius:50%;background:var(--dark);border:6px solid var(--orange);display:flex;align-items:center;justify-content:center}
.client-name{text-align:center;font-size:20px;color:var(--dark)}
.client-text{font-style:italic;font-size:16px;line-height:24px;color:#444;text-align:justify}
.review-card{left:438px;top:1904px;width:325px;height:320px;background:var(--white);box-shadow:0 2px 14px rgba(0,0,0,.12)}
.dot{position:absolute;top:2270px;width:21px;height:21px;border-radius:50%;background:var(--grey)}

.insta-band{left:0;top:2376px;width:1200px;height:700px;background:linear-gradient(135deg,#fbb255 0%,#faa641 55%,#f59a30 100%)}
.tile{position:absolute;width:229px}

.footer-col-title{font-size:24px;color:var(--orange)}
.footer-links{list-style:none;font-size:16px;line-height:25px;color:var(--white)}
</style>
</head>
<body>

<!-- Hero -->
<div class="abs photo hero-photo" role="img" aria-label="Photo of a client receiving a laser facial treatment from a gloved technician"></div>
<div class="abs hero-shade"></div>
<svg class="abs" style="left:0;top:520px" width="1200" height="140" viewBox="0 520 1200 140">
  <path d="M0 540 Q600 680 1200 540 L1200 660 L0 660 Z" fill="var(--white)"/>
  <path d="M0 540 Q600 680 1200 540" fill="none" stroke="var(--orange)" stroke-width="5"/>
</svg>

<header class="abs nav">
  <div class="brand" style="left:46px;top:20px;font-size:28px;color:var(--dark)">
    <span class="brand-dot"></span>WILLOW GLOW
  </div>
  <nav class="nav-links">
    <span>Home</span><span>Services</span><span>Pricing</span><span>About</span><span>Blog</span><span>Contact</span>
  </nav>
  <div class="btn btn-orange" style="left:811px;top:22px;width:130px;height:34px">Book Online</div>
</header>

<h1 class="abs heading hero-title">Your Skin <span>Deserves It</span></h1>
<p class="abs hero-sub">Laser center &amp; medispa located in downtown phoenix, tempe, tucson, &amp; yuma.</p>
<div class="btn btn-orange" style="left:111px;top:368px;width:130px;height:33px">Book Online</div>
<div class="btn btn-ghost" style="left:266px;top:368px;width:130px;height:33px">Show Deal</div>

<div class="round-icon" style="left:569px;top:585px">
  <svg width="26" height="26" viewBox="0 0 26 26" fill="none" stroke="var(--orange)" stroke-width="3" stroke-linecap="round" stroke-linejoin="round"><path d="M6 6l7 7 7-7M6 13l7 7 7-7"/></svg>
</div>

<!-- Services -->
<h2 class="abs heading section-title" style="top:692px">What We Offer</h2>

<div class="abs card-img" style="left:111px;top:768px;background:radial-gradient(ellipse 140px 120px at 120px 130px,#e2b9a1,rgba(226,185,161,0) 75%),linear-gradient(160deg,#8a7a70 0%,#c7a48e 45%,#a7826c 100%)" role="img" aria-label="Photofacial treatment photo"></div>
<div class="abs card-img" style="left:361px;top:768px;background:radial-gradient(ellipse 150px 130px at 110px 110px,#d9a88c,rgba(217,168,140,0) 75%),radial-gradient(circle 40px at 190px 160px,#f0d0a8,rgba(240,208,168,0) 90%),linear-gradient(160deg,#5c3f31 0%,#a97a62 50%,#7a5443 100%)" role="img" aria-label="Botox injection treatment photo"></div>
<div class="abs card-img" style="left:611px;top:768px;background:radial-gradient(ellipse 120px 90px at 130px 60px,#c89c88,rgba(200,156,136,0) 75%),radial-gradient(ellipse 70px 90px at 80px 170px,#f2f2f2,rgba(242,242,242,0) 80%),linear-gradient(160deg,#2c2624 0%,#7c6b64 50%,#3b302d 100%)" role="img" aria-label="Laser hair removal treatment photo"></div>
<div class="abs card-img" style="left:860px;top:768px;background:radial-gradient(ellipse 120px 90px at 140px 60px,#e6e6e8,rgba(230,230,232,0) 75%),radial-gradient(ellipse 110px 70px at 100px 185px,#c9a28c,rgba(201,162,140,0) 80%),linear-gradient(160deg,#d4d6d8 0%,#8d8784 55%,#3a3433 100%)" role="img" aria-label="Facial and peel treatment photo"></div>

<div class="abs card-title" style="left:111px;top:1008px">Photofacials</div>
<div class="abs card-title" style="left:361px;top:1008px">Botox Injections</div>
<div class="abs card-title" style="left:611px;top:1008px">Laser Hair Removal</div>
<div class="abs card-title" style="left:860px;top:1008px">Facials &amp; Peels</div>
<div class="abs card-line" style="left:190px;top:1045px"></div>
<div class="abs card-line" style="left:440px;top:1045px"></div>
<div class="abs card-line" style="left:690px;top:1045px"></div>
<div class="abs card-line" style="left:939px;top:1045px"></div>

<div class="btn btn-orange" style="left:535px;top:1093px;width:131px;height:32px">View More</div>

<!-- About -->
<section class="abs about-band"></section>
<div class="abs" style="left:111px;top:1297px;width:365px;height:277px;background:radial-gradient(ellipse 140px 80px at 60px 140px,#e0488e,rgba(224,72,142,0) 75%),radial-gradient(ellipse 170px 110px at 230px 150px,#efcdb6,rgba(239,205,182,0) 75%),linear-gradient(150deg,#f2eeec 0%,#d9b29c 45%,#8a5a3e 100%);box-shadow:0 4px 12px rgba(0,0,0,.15)" role="img" aria-label="Technician with pink gloves treating a client's face"></div>
<div class="abs" style="left:366px;top:1436px;width:233px;height:202px;background:var(--white);padding:6px;box-shadow:0 4px 12px rgba(0,0,0,.15)">
  <div style="width:100%;height:100%;background:radial-gradient(circle 22px at 95px 65px,#ff7a7a,rgba(255,122,122,0) 90%),radial-gradient(ellipse 90px 70px at 60px 150px,#e9b3c2,rgba(233,179,194,0) 80%),linear-gradient(150deg,#6d6a6e 0%,#c9a6a0 45%,#8e6d70 100%)" role="img" aria-label="Close-up of a laser device on a client's cheek"></div>
</div>
<h2 class="abs heading about-title">About Willow Glow &amp; Laser</h2>
<div class="abs about-text">
  <p>At Willow Glow &amp; Laser, we’ve always believed that caring about your skin and your appearance is not selfish, it is self-care. It’s time to be proud of the steps you take to look your best and it’s time you ask for the best. Your skin deserves it.</p>
  <p>Willow Glow brings to you the latest technology, techniques, and the best professionals to deliver the results you want guaranteed. It’s time to cross out the judgment, the labels, the hesitation, and the regrets. We offer clinic locations in Tucson, AZ, Phoenix, AZ, Tempe, AZ and Yuma, AZ.</p>
</div>
<div class="btn btn-dark" style="left:638px;top:1620px;width:132px;height:32px">Learn More</div>

<!-- Testimonials -->
<h2 class="abs heading section-title" style="top:1814px">What Our Happy Clients Say</h2>
<div class="abs review-card"></div>

<div class="quote-badge" style="left:202px;top:1931px"><svg width="48" height="40" viewBox="0 0 48 40" fill="var(--white)"><path d="M4 38V22C4 10 10 3 20 1l2 5c-6 2-9 6-9 12h8v20zM28 38V22c0-12 6-19 16-21l2 5c-6 2-9 6-9 12h8v20z"/></svg></div>
<div class="quote-badge" style="left:550px;top:1931px"><svg width="48" height="40" viewBox="0 0 48 40" fill="var(--white)"><path d="M4 38V22C4 10 10 3 20 1l2 5c-6 2-9 6-9 12h8v20zM28 38V22c0-12 6-19 16-21l2 5c-6 2-9 6-9 12h8v20z"/></svg></div>
<div class="quote-badge" style="left:899px;top:1931px"><svg width="48" height="40" viewBox="0 0 48 40" fill="var(--white)"><path d="M4 38V22C4 10 10 3 20 1l2 5c-6 2-9 6-9 12h8v20zM28 38V22c0-12 6-19 16-21l2 5c-6 2-9 6-9 12h8v20z"/></svg></div>

<div class="abs heading client-name" style="left:111px;top:2046px;width:282px">Mara L</div>
<div class="abs heading client-name" style="left:438px;top:2046px;width:325px">Tessa R</div>
<div class="abs heading client-name" style="left:806px;top:2046px;width:283px">Nina K</div>

<p class="abs client-text" style="left:111px;top:2082px;width:282px">"I have been going to Willow Glow &amp; Laser for 2 years now. I am very pleased with my laser hair reduction results."</p>
<p class="abs client-text" style="left:457px;top:2082px;width:282px">"Lena is my technician and I love her! Always goes the extra mile to make sure areas are covered, and that I'm getting the best result. I couldn't be happier."</p>
<p class="abs client-text" style="left:806px;top:2082px;width:283px">"Lena is my technician and I love her! Always goes the extra mile to make sure areas are covered, and that I'm getting the best result. I couldn't be happier."</p>

<span class="dot" style="left:537px"></span>
<span class="dot" style="left:572px;background:var(--orange)"></span>
<span class="dot" style="left:606px"></span>
<span class="dot" style="left:640px"></span>

<!-- Instagram -->
<section class="abs insta-band"></section>
<h2 class="abs heading section-title" style="top:2450px;color:var(--white)">Instagram Feed</h2>
<div class="tile" style="left:111px;top:2527px;height:345px;background:radial-gradient(ellipse 90px 70px at 70px 60px,#8c7867,rgba(140,120,103,0) 80%),radial-gradient(ellipse 100px 80px at 130px 260px,#9a8574,rgba(154,133,116,0) 80%),linear-gradient(160deg,#2f2a27 0%,#4a413b 50%,#2a2522 100%)" role="img" aria-label="Instagram post: smiling staff member with a client"></div>
<div class="tile" style="left:361px;top:2527px;height:163px;border:4px solid var(--white);background:radial-gradient(ellipse 50px 60px at 50px 60px,#2a2a2a,rgba(42,42,42,0) 80%),radial-gradient(ellipse 60px 50px at 120px 80px,#b48e78,rgba(180,142,120,0) 80%),linear-gradient(160deg,#ece9e5 0%,#bfb6ae 55%,#3c3633 100%)" role="img" aria-label="Instagram post: client holding a hand mirror"></div>
<div class="tile" style="left:611px;top:2527px;height:163px;background:radial-gradient(ellipse 70px 50px at 140px 110px,#6e625b,rgba(110,98,91,0) 80%),linear-gradient(160deg,#2a2624 0%,#3d3633 55%,#241f1d 100%)" role="img" aria-label="Instagram post: technician performing a treatment"></div>
<div class="tile" style="left:860px;top:2527px;height:163px;background:radial-gradient(ellipse 50px 70px at 70px 80px,#5a4e47,rgba(90,78,71,0) 80%),radial-gradient(ellipse 50px 70px at 160px 80px,#7d7069,rgba(125,112,105,0) 80%),linear-gradient(160deg,#3b3633 0%,#2c2725 100%)" role="img" aria-label="Instagram post: two staff members holding gift cards"></div>
<div class="tile" style="left:361px;top:2708px;height:164px;background:radial-gradient(ellipse 60px 60px at 60px 50px,#6c5d52,rgba(108,93,82,0) 80%),radial-gradient(ellipse 60px 50px at 170px 120px,#5d534d,rgba(93,83,77,0) 80%),linear-gradient(160deg,#3a3431 0%,#27221f 100%)" role="img" aria-label="Instagram post: technician treating a client"></div>
<div class="tile" style="left:611px;top:2708px;height:164px;background:radial-gradient(ellipse 80px 40px at 110px 40px,#5e5650,rgba(94,86,80,0) 80%),radial-gradient(ellipse 60px 50px at 100px 120px,#4a4341,rgba(74,67,65,0) 80%),linear-gradient(160deg,#3a3431 0%,#2a2523 100%)" role="img" aria-label="Instagram post: staff member using a tablet in the clinic"></div>
<div class="tile" style="left:860px;top:2708px;height:164px;background:radial-gradient(ellipse 60px 60px at 90px 80px,#7a685c,rgba(122,104,92,0) 80%),linear-gradient(160deg,#2e2927 0%,#3f3835 50%,#221e1c 100%)" role="img" aria-label="Instagram post: client holding a mirror"></div>

<!-- Footer -->
<svg class="abs" style="left:0;top:2940px" width="1200" height="421" viewBox="0 2940 1200 421">
  <path d="M0 3038 Q600 2868 1200 3038 L1200 3361 L0 3361 Z" fill="var(--dark)"/>
  <path d="M0 3038 Q600 2868 1200 3038" fill="none" stroke="var(--orange)" stroke-width="5"/>
</svg>
<div class="round-icon" style="left:569px;top:2913px">
  <svg width="26" height="26" viewBox="0 0 26 26" fill="none" stroke="var(--orange)" stroke-width="3" stroke-linecap="round" stroke-linejoin="round"><path d="M6 13l7-7 7 7M6 20l7-7 7 7"/></svg>
</div>

<footer>
  <div class="abs" style="left:169px;top:3125px;width:46px;height:46px;border-radius:50%;background:var(--orange)"></div>
  <div class="abs heading" style="left:82px;top:3190px;width:220px;text-align:center;font-size:26px;line-height:30px;font-weight:800;color:var(--white);letter-spacing:1px">WILLOW GLOW<br>&amp; LASER</div>
  <div class="abs" style="left:119px;top:3278px;display:flex;align-items:center;gap:10px;font-size:16px;color:var(--white)">
    <svg width="17" height="13" viewBox="0 0 17 13"><rect width="17" height="13" rx="2" fill="var(--orange)"/><path d="M1 1l7.5 6L16 1" fill="none" stroke="var(--dark)" stroke-width="1.6"/></svg>
    hello@willowglowlaser.example
  </div>

  <h3 class="abs heading footer-col-title" style="left:395px;top:3114px">Quick Links</h3>
  <ul class="abs footer-links" style="left:396px;top:3163px">
    <li>Home</li><li>About</li><li>Services</li><li>Pricing</li><li>Blog</li><li>Contact Us</li>
  </ul>

  <h3 class="abs heading footer-col-title" style="left:578px;top:3114px">Other Links</h3>
  <ul class="abs footer-links" style="left:578px;top:3163px">
    <li>Faqs</li><li>Our Location</li><li>Privacy Policy</li><li>Cookie Policy</li><li>Sitemap</li>
  </ul>

  <h3 class="abs heading footer-col-title" style="left:759px;top:3114px">Subscribe To Our Newsletter</h3>
  <div class="abs" style="left:759px;top:3167px;width:330px;height:49px;border:1px solid #8a8a8a;display:flex">
    <span style="flex:1;padding:15px 16px;font-style:italic;font-size:16px;color:#bbb">example@gmail.com</span>
    <span style="width:55px;background:var(--orange);display:flex;align-items:center;justify-content:center">
      <svg width="22" height="22" viewBox="0 0 22 22"><path d="M2 10L20 2 13 20 10 12Z" fill="var(--dark)"/></svg>
    </span>
  </div>
  <p class="abs" style="left:759px;top:3294px;font-size:14px;color:var(--white)">© 2024 <span style="color:var(--orange)">Willow Glow &amp; Laser.</span> All Rights Reserved.</p>
</footer>

</body>
</html>
```